RW Framewell Inc Business cards

We need business cards using our existing logo but slightly modified. Right now the logo says RW Loadbearing Masonry. We want to keep the RW part of the design, but replace the Structural Concrete portion with "FRAMEWELL". Please see the attached file.
Ideally this would be a blank template so we can add Different Names, titles, and phone numbers later.
On the one side we want only the logo and on the other side the detail. I'm attaching an example for you to see.
Please reach out with any other questions. Our address and other details will be given out once we find a design we like.

Target Market(s)

Construction Industry

```html
<!DOCTYPE html>
<html lang="en">
<head>
<meta charset="utf-8">
<title>RW Framewell Inc Business Cards</title>
<link rel="stylesheet" href="https://fonts.googleapis.com/css2?family=Russo+One&family=Arimo:wght@400&display=swap">
<style>
  :root {
    --brand-blue: #1c75bc;
    --card-white: #ffffff;
    --text-grey: #4a4a4d;
    --backdrop: #e4e5e6;
  }
  html, body {
    margin: 0;
    padding: 0;
    width: 1200px;
    height: 900px;
    overflow: hidden;
    background: var(--backdrop);
  }
  .stage {
    position: relative;
    width: 1200px;
    height: 900px;
  }
  .card {
    position: absolute;
    top: 216px;
    width: 309px;
    height: 501px;
    box-sizing: border-box;
  }
  .card--front {
    left: 279px;
    background: var(--brand-blue);
    border-radius: 0 70px 0 70px;
  }
  .card--back {
    left: 617px;
    background: var(--card-white);
    border-radius: 70px 0 70px 0;
  }
  .wordmark {
    position: absolute;
    font-family: "Russo One", sans-serif;
    font-weight: 400;
    margin: 0;
    line-height: 1;
  }
  .wordmark__initials {
    display: block;
    font-size: 104px;
    letter-spacing: 14px;
  }
  .wordmark__name {
    display: block;
    font-size: 24px;
    letter-spacing: 5.2px;
    margin-top: 6px;
  }
  .card--front .wordmark {
    left: 38px;
    top: 190px;
    color: var(--card-white);
  }
  .card--back .wordmark {
    left: 40px;
    top: 96px;
    color: var(--brand-blue);
  }
  .card--back .wordmark__initials {
    font-size: 98px;
    letter-spacing: 13px;
  }
  .card--back .wordmark__name {
    font-size: 22px;
    letter-spacing: 5px;
  }
  .holder {
    position: absolute;
    left: 37px;
    top: 322px;
  }
  .holder__name {
    margin: 0;
    font-family: "Russo One", sans-serif;
    font-size: 19px;
    line-height: 1;
    color: var(--brand-blue);
    letter-spacing: 0.3px;
  }
  .holder__title {
    margin: 3px 0 0;
    font-family: "Arimo", sans-serif;
    font-size: 14.5px;
    color: var(--text-grey);
  }
  .contact {
    position: absolute;
    left: 37px;
    top: 397px;
    margin: 0;
    padding: 0;
    list-style: none;
    font-family: "Arimo", sans-serif;
    font-size: 14.5px;
    color: var(--text-grey);
  }
  .contact__item {
    display: flex;
    align-items: center;
    height: 19px;
  }
  .contact__icon {
    width: 15px;
    height: 15px;
    margin-right: 6px;
    flex: none;
  }
</style>
</head>
<body>
<main class="stage">
  <section class="card card--front" aria-label="Card front">
    <p class="wordmark">
      <span class="wordmark__initials">RW</span>
      <span class="wordmark__name">FRAMEWELL</span>
    </p>
  </section>

  <section class="card card--back" aria-label="Card back">
    <p class="wordmark">
      <span class="wordmark__initials">RW</span>
      <span class="wordmark__name">FRAMEWELL</span>
    </p>

    <div class="holder">
      <h1 class="holder__name">DANIEL MARSH</h1>
      <p class="holder__title">Managing Director</p>
    </div>

    <ul class="contact">
      <li class="contact__item">
        <svg class="contact__icon" viewBox="0 0 24 24" aria-hidden="true">
          <path fill="var(--brand-blue)" d="M6.6 10.8a15 15 0 0 0 6.6 6.6l2.2-2.2c.3-.3.7-.4 1-.2 1.1.4 2.3.6 3.6.6.6 0 1 .4 1 1V20c0 .6-.4 1-1 1A17 17 0 0 1 3 4c0-.6.4-1 1-1h3.5c.6 0 1 .4 1 1 0 1.3.2 2.5.6 3.6.1.3 0 .7-.2 1z"/>
          <path fill="none" stroke="var(--brand-blue)" stroke-width="1.8" d="M14 3a7 7 0 0 1 7 7M14 7a3 3 0 0 1 3 3"/>
        </svg>
        <span>021-555 308 416</span>
      </li>
      <li class="contact__item">
        <svg class="contact__icon" viewBox="0 0 24 24" aria-hidden="true">
          <rect x="1" y="5" width="22" height="14" fill="var(--brand-blue)"/>
          <path fill="none" stroke="#fff" stroke-width="1.6" d="M1.5 5.5 12 13 22.5 5.5M1.5 18.5l8-7M22.5 18.5l-8-7"/>
        </svg>
        <span>hello@framewell.example</span>
      </li>
      <li class="contact__item">
        <svg class="contact__icon" viewBox="0 0 24 24" aria-hidden="true">
          <g fill="none" stroke="var(--brand-blue)" stroke-width="1.8">
            <circle cx="12" cy="12" r="10"/>
            <ellipse cx="12" cy="12" rx="4.5" ry="10"/>
            <path d="M2 12h20M4 7h16M4 17h16"/>
          </g>
        </svg>
        <span>www.framewell.example</span>
      </li>
    </ul>
  </section>
</main>
</body>
</html>
```